Professional Photography Business cards

I need business cards that include my logo which I have uploaded. I run a photography business. I am open to ideas but I would like one side to have my logo and the other side to have my contact info. I don't have a website made but I do own a website domain. I have uploaded 2 different logo color schemes. My business colors are Blue, black , and white.

Business Name
Business Phone Number
Business Email
Business Website address
Instagram

Industry/Entity Type

Professional Photography

Contact Information for Business Card

Phone Number: 916-384-7702 email: info@tlane-studio.example Instagram: @t.lanestudio website doman- www.tlane-studio.example

Requirements
Must have
• I like the idea of a business card with a full black background front and back of card. My colors must include royal blue, black, and white

```html
<!DOCTYPE html>
<html lang="en">
<head>
<meta charset="utf-8">
<title>T. Lane Studio – Business Cards</title>
<link href="https://fonts.googleapis.com/css2?family=Roboto:wght@400;500;700&display=swap" rel="stylesheet">
<style>
  :root {
    --backdrop: #2c2c2d;
    --card: #1b1b1c;
    --royal-blue: #2b36a8;
    --white: #ffffff;
    --emboss: #2a2a2b;
    --emboss-ring: #5a5a5c;
  }
  * { margin: 0; padding: 0; box-sizing: border-box; }
  html, body {
    width: 1200px; height: 1059px; overflow: hidden;
    background: var(--backdrop);
    font-family: "Roboto", Arial, sans-serif;
  }
  .canvas { position: relative; width: 1200px; height: 1059px; }
  .card {
    position: absolute; left: 254px; width: 692px; height: 393px;
    background: var(--card); border-radius: 20px; overflow: hidden;
    box-shadow: 0 12px 24px rgba(0,0,0,0.45);
  }
  .card--front { top: 100px; }
  .card--back { top: 537px; }

  .wordmark { position: absolute; display: flex; align-items: center; gap: 18px; }
  .wordmark__name { font-weight: 500; white-space: nowrap; line-height: 1; }
  .wordmark__ring { border-radius: 50%; flex: none; }

  .card--front .wordmark { left: 50%; top: 50%; transform: translate(-46%, -50%); }
  .card--front .wordmark__name { font-size: 52px; color: var(--emboss); text-shadow: 0 1px 0 #111; }
  .card--front .wordmark__ring { width: 94px; height: 94px; border: 5px solid var(--emboss-ring); }

  .card--back .wordmark { right: 34px; top: 50px; }
  .card--back .wordmark__name { font-size: 40px; color: var(--royal-blue); }
  .card--back .wordmark__ring { width: 68px; height: 68px; border: 4px solid var(--white); }

  .accent-bar { position: absolute; left: 0; top: 221px; width: 11px; height: 39px; background: var(--royal-blue); }
  .person__name { position: absolute; left: 33px; top: 206px; font-size: 28px; font-weight: 700; color: var(--royal-blue); line-height: 1; }
  .person__title { position: absolute; left: 33px; top: 239px; font-size: 16.5px; color: var(--white); line-height: 1.2; }

  .contact { position: absolute; left: 33px; top: 279px; list-style: none; }
  .contact li { display: flex; align-items: center; height: 21.5px; font-size: 16.5px; color: var(--white); }
  .contact svg { width: 11px; height: 11px; margin-right: 9px; flex: none; }
  .contact .dot { width: 10px; height: 10px; border-radius: 50%; background: var(--royal-blue); margin-right: 10px; flex: none; }
</style>
</head>
<body>
<main class="canvas">
  <section class="card card--front" aria-label="Card front">
    <div class="wordmark">
      <span class="wordmark__name">T. Lane Studio</span>
      <span class="wordmark__ring"></span>
    </div>
  </section>

  <section class="card card--back" aria-label="Card back">
    <div class="wordmark">
      <span class="wordmark__name">T. Lane Studio</span>
      <span class="wordmark__ring"></span>
    </div>

    <span class="accent-bar"></span>
    <h1 class="person__name">Tessa Lane</h1>
    <p class="person__title">Managing Director</p>

    <ul class="contact">
      <li>
        <svg viewBox="0 0 24 24" aria-hidden="true"><path fill="#2b36a8" d="M6.6 10.8a15.1 15.1 0 0 0 6.6 6.6l2.2-2.2c.3-.3.7-.4 1-.2 1.1.4 2.3.6 3.6.6.6 0 1 .4 1 1V20c0 .6-.4 1-1 1A17 17 0 0 1 3 4c0-.6.4-1 1-1h3.5c.6 0 1 .4 1 1 0 1.3.2 2.5.6 3.6.1.3 0 .7-.2 1z"/></svg>
        916-384-7702
      </li>
      <li>
        <svg viewBox="0 0 24 24" aria-hidden="true"><path fill="#2b36a8" d="M2 5h20v14H2z"/><path fill="none" stroke="#1b1b1c" stroke-width="2" d="M2 5l10 8 10-8M2 19l7-7M22 19l-7-7"/></svg>
        info@tlane-studio.example
      </li>
      <li>
        <svg viewBox="0 0 24 24" aria-hidden="true"><circle cx="12" cy="12" r="10" fill="#2b36a8"/><path fill="none" stroke="#1b1b1c" stroke-width="1.5" d="M2 12h20M12 2c3 3 3 17 0 20M12 2c-3 3-3 17 0 20"/></svg>
        www.tlane-studio.example
      </li>
      <li>
        <span class="dot"></span>
        @t.lanestudio
      </li>
    </ul>
  </section>
</main>
</body>
</html>
```